Varnik Holdings — Business Card Design Brief
Overview
Design a double-sided business card for Varnik Holdings that highlights our two service arms: Varnik Communications (telecommunications) and Varnik Energy (business energy solutions). The card should feel smart and stand out when handed to clients.

Objectives
Showcase our areas of specialty clearly.
Reflect the overall Varnik / Varnik Holdings brand while acknowledging both arms.
Explore using both logos (Communications + Energy) or one unified logo, depending on the design.

Deliverables
One double-sided business card design (front + back).

Content & Copy
Front (preferred): Logo: Varnik / Varnik Holdings
Descriptor: Business Communications | Business Energy
Back:My contact details and company details
Core products: Business Mobile • Telephony • Internet • Business Energy Solutions

Brand & Visual Direction
We have a group logo currently tailored more toward telecoms, plus a separate Varnik Energy logo.
Please explore layouts that use both logos or just one, whichever works best.
Color: I wouldn't mind seeing an option using our the Blue/Purple gradient from our website (varnik-example.co.uk), but also open to non-gradient approaches and other colours..

Overall look: Smart, modern, and distinctive.
Format & Print Specs
Double-sided business card format. (Use a standard size

Must-Haves
Front: Varnik wording or Varnik Holdings wording with atleast 1 logo also on front “Business Communications | Business Energy.”

Back: Contact + company details and core products.
A design that stands out while remaining professional.

Nice-to-Have Options
A gradient version using our site’s Blue/Purple gradient.
A non-gradient version.
A dual-logo treatment versus a single-logo treatment.

Thanks
Owen

```html
<!DOCTYPE html>
<html lang="en">
<head>
<meta charset="utf-8">
<title>Varnik Holdings Business Card</title>
<link href="https://fonts.googleapis.com/css2?family=Arimo:wght@400;700&display=swap" rel="stylesheet">
<style>
  :root {
    --bg: #e4e4e4;
    --paper: #ffffff;
    --navy: #1c1663;
    --ink: #2a2a2a;
    --grey: #6b6b6b;
    --slate: #2b2b2b;
    --mark-dark: #141414;
    --mark-silver: #a3a3a3;
    --comm-blue: #1e8fd6;
    --energy-green: #7cb51f;
    --rule-light: #cfcfcf;
  }
  * { box-sizing: border-box; margin: 0; padding: 0; }
  html, body { width: 1200px; height: 1200px; overflow: hidden; }
  body {
    background: var(--bg);
    font-family: "Arimo", Arial, sans-serif;
    position: relative;
  }
  .card {
    position: absolute;
    left: 262px;
    width: 688px;
    height: 393px;
  }
  .card-front { top: 159px; background: var(--paper); }
  .card-back { top: 653px; background: var(--slate); }

  .identity {
    position: absolute;
    right: 341px;
    top: 150px;
    text-align: right;
  }
  .identity .name {
    color: var(--navy);
    font-weight: 700;
    font-size: 26px;
    letter-spacing: 0.5px;
    line-height: 30px;
  }
  .identity .role { color: var(--grey); font-size: 15px; line-height: 22px; }
  .identity .address { color: var(--ink); font-size: 16px; line-height: 21px; }

  .front-rule {
    position: absolute;
    left: 369px;
    top: 153px;
    width: 1px;
    height: 82px;
    background: var(--navy);
  }
  .contacts {
    position: absolute;
    left: 385px;
    top: 151px;
    list-style: none;
  }
  .contacts li {
    display: flex;
    align-items: center;
    gap: 8px;
    font-size: 16px;
    line-height: 20.5px;
    color: var(--ink);
  }
  .contacts svg { width: 13px; height: 13px; fill: var(--navy); }

  .products {
    position: absolute;
    left: 0; right: 0;
    top: 327px;
    text-align: center;
    font-size: 17px;
    color: var(--ink);
  }

  .brand {
    position: absolute;
    top: 92px;
    width: 300px;
    text-align: center;
  }
  .brand-comm { left: 52px; }
  .brand-energy { left: 410px; }
  .brand .disc {
    width: 96px; height: 96px;
    margin: 0 auto 22px;
    border-radius: 50%;
  }
  .brand-comm .disc { background: var(--mark-dark); }
  .brand-energy .disc { background: var(--mark-silver); }
  .brand .wordmark {
    font-weight: 700;
    font-size: 56px;
    line-height: 60px;
    letter-spacing: 1px;
  }
  .brand-comm .wordmark { color: var(--mark-dark); }
  .brand-energy .wordmark { color: var(--mark-silver); }
  .brand .descriptor { margin-top: 16px; font-size: 15.5px; }
  .brand-comm .descriptor { color: var(--comm-blue); }
  .brand-energy .descriptor { color: var(--energy-green); letter-spacing: 3px; font-weight: 700; font-size: 14.5px; }

  .back-rule {
    position: absolute;
    left: 355px;
    top: 101px;
    width: 1px;
    height: 199px;
    background: var(--rule-light);
  }
</style>
</head>
<body>
  <section class="card card-front">
    <div class="identity">
      <p class="name">DANIEL HART</p>
      <p class="role">President</p>
      <p class="address">1420 Alder Court<br>Kelmont, Canada 20418</p>
    </div>
    <div class="front-rule"></div>
    <ul class="contacts">
      <li><svg viewBox="0 0 24 24"><path d="M6.6 10.8a15 15 0 0 0 6.6 6.6l2.2-2.2c.3-.3.7-.4 1-.2 1.1.4 2.3.6 3.6.6.6 0 1 .4 1 1V20c0 .6-.4 1-1 1A17 17 0 0 1 3 4c0-.6.4-1 1-1h3.5c.6 0 1 .4 1 1 0 1.3.2 2.5.6 3.6.1.3 0 .7-.2 1z"/></svg>555-014-2276</li>
      <li><svg viewBox="0 0 24 24"><path d="M7 1h10a2 2 0 0 1 2 2v18a2 2 0 0 1-2 2H7a2 2 0 0 1-2-2V3a2 2 0 0 1 2-2zm0 3v15h10V4z"/></svg>555-019-8841</li>
      <li><svg viewBox="0 0 24 24"><path d="M2 5h20v14H2zm2 2v.5l8 5 8-5V7l-8 5z"/></svg>info@VARNIK.com</li>
      <li><svg viewBox="0 0 24 24"><path d="M12 2a10 10 0 1 0 0 20 10 10 0 0 0 0-20zm-1 17.9A8 8 0 0 1 4.1 11H8c.2 3 1.2 6 3 8.9zM13 4.1A8 8 0 0 1 19.9 11H16c-.2-3-1.2-5-3-6.9z"/></svg>www.VARNIK.com</li>
    </ul>
    <p class="products">Business Mobile &nbsp;•&nbsp; Telephony &nbsp;•&nbsp; Internet &nbsp;•&nbsp; Business Energy Solutions</p>
  </section>

  <section class="card card-back">
    <div class="brand brand-comm">
      <div class="disc"></div>
      <p class="wordmark">VARNIK</p>
      <p class="descriptor">BUSINESS COMMUNICATIONS</p>
    </div>
    <div class="back-rule"></div>
    <div class="brand brand-energy">
      <div class="disc"></div>
      <p class="wordmark">VARNIK</p>
      <p class="descriptor">BUSINESS ENERGY</p>
    </div>
  </section>
</body>
</html>
```